Real Estate Business Card

On the front side I want to have my info, my brokerage info.
On the back side I want have my complany’s logo, website and Facebook link. I will provide all this once I select a design.

I would like to see Black background and gold text, Dark Blue and gold text and White and blue text designs

Font styles to use
Sans Serif
Script

```html
<!DOCTYPE html>
<html lang="en">
<head>
<meta charset="utf-8">
<title>Northpeak Realty – Business Card</title>
<link href="https://fonts.googleapis.com/css2?family=Montserrat:wght@800&family=Roboto:wght@400;700&display=swap" rel="stylesheet">
<style>
  :root {
    --backdrop: #2a2a2d;
    --card: #1b1b1d;
    --brand-red: #e8393f;
    --gold: #e9c86b;
    --ink-light: #f2f2f2;
  }
  * { margin: 0; padding: 0; box-sizing: border-box; }
  html, body { width: 1200px; height: 900px; overflow: hidden; }
  body {
    background: var(--backdrop);
    display: flex;
    flex-direction: column;
    align-items: center;
    justify-content: center;
    gap: 40px;
    font-family: "Roboto", Arial, sans-serif;
  }
  .card {
    position: relative;
    width: 700px;
    height: 400px;
    background: var(--card);
    box-shadow: 0 14px 30px rgba(0,0,0,.45);
    overflow: hidden;
  }
  /* back side */
  .card-back .brand-mark {
    position: absolute;
    right: 70px;
    bottom: 70px;
    display: flex;
    align-items: center;
    gap: 14px;
    font-family: "Montserrat", Arial, sans-serif;
    font-weight: 800;
    font-size: 44px;
    color: var(--brand-red);
    text-transform: uppercase;
  }
  .brand-square {
    width: 30px; height: 30px;
    background: var(--brand-red);
  }
  /* front side */
  .card-front .wordmark {
    position: absolute;
    left: 60px;
    top: 95px;
    font-family: "Montserrat", Arial, sans-serif;
    font-weight: 800;
    font-size: 44px;
    color: var(--brand-red);
    text-transform: uppercase;
  }
  .accent {
    position: absolute;
    left: 0; top: 0;
  }
  .name-band {
    position: absolute;
    right: 28px;
    top: 178px;
    text-align: right;
    color: var(--gold);
    text-transform: uppercase;
    font-weight: 700;
  }
  .name-band .person { font-size: 28px; letter-spacing: .5px; }
  .name-band .role { font-size: 18px; margin-top: 2px; }
  .contact-list {
    position: absolute;
    left: 44px;
    top: 200px;
    list-style: none;
    color: var(--ink-light);
    font-size: 19px;
    line-height: 1.25;
  }
  .contact-list li {
    display: flex;
    align-items: flex-start;
    gap: 16px;
    margin-bottom: 6px;
  }
  .contact-list svg { flex: none; width: 18px; height: 18px; margin-top: 3px; }
</style>
</head>
<body>

  <section class="card card-back" aria-label="Card back">
    <div class="brand-mark"><span class="brand-square"></span>Northpeak</div>
  </section>

  <section class="card card-front" aria-label="Card front">
    <div class="wordmark">Northpeak Realty</div>

    <svg class="accent" width="700" height="400" viewBox="0 0 700 400" aria-hidden="true">
      <line x1="40" y1="175" x2="470" y2="175" stroke="var(--brand-red)" stroke-width="2"/>
      <polygon points="440,175 700,175 700,240 400,240" fill="var(--brand-red)"/>
    </svg>

    <div class="name-band">
      <div class="person">Dana Whitfield</div>
      <div class="role">CEO/Founder</div>
    </div>

    <ul class="contact-list">
      <li>
        <svg viewBox="0 0 18 18" aria-hidden="true"><path d="M9 1a6 6 0 0 0-6 6c0 4.5 6 10 6 10s6-5.5 6-10a6 6 0 0 0-6-6z" fill="var(--gold)"/><circle cx="9" cy="7" r="2.2" fill="var(--card)"/></svg>
        <span>2140 Larchmont Way<br>Fairbanks, Alaska 99701</span>
      </li>
      <li>
        <svg viewBox="0 0 18 18" aria-hidden="true"><path d="M4 1l3 4-2 2c1 2.5 3.5 5 6 6l2-2 4 3-2 3C8 17 1 10 1 3z" fill="var(--gold)"/></svg>
        <span>555 204 7813</span>
      </li>
      <li>
        <svg viewBox="0 0 18 18" aria-hidden="true"><rect x="1" y="4" width="16" height="11" fill="var(--gold)"/><path d="M1 4l8 6 8-6" stroke="var(--card)" stroke-width="1.5" fill="none"/></svg>
        <span>dana@northpeak.com</span>
      </li>
      <li>
        <svg viewBox="0 0 18 18" aria-hidden="true"><circle cx="9" cy="9" r="8" fill="var(--gold)"/><path d="M1 9h16M9 1c-3 3-3 13 0 16M9 1c3 3 3 13 0 16" stroke="var(--card)" stroke-width="1.2" fill="none"/></svg>
        <span>www.northpeak.com</span>
      </li>
      <li>
        <svg viewBox="0 0 18 18" aria-hidden="true"><circle cx="9" cy="9" r="8" fill="var(--gold)"/></svg>
        <span>/northpeak</span>
      </li>
    </ul>
  </section>

</body>
</html>
```